New Business Card for Web Design/Internet Marketing Company

Looking for a great looking new business card. We are a 10 year old web design, internet marketing and website management company that works mostly with small businesses.

Our new card needs to better match the colors and style of our website, be bold, extremely usable and slightly edgy.

Target Market(s)

Small/Medium businesses that have websites

Industry/Entity Type

Internet

Requirements
Must have
• Front and back design, full color, rounded corners please

Must use the colors/style of our website (JPG provided)

INFO FOR CARDS (as readable as possible please)
Mark Lenner
President/CEO
mark@trelvanmedia.example
Phone: 520-381-7459
Toll Free: 866-381-7459
Address: 4315 W. Calloway Ave. Ste. 140, Tucson, AZ 85792

THINGS I WANT TO PROMOTE (if there is room):
1. Our Website - www.trelvanmedia.example

2. Social Media
Twitter: @trelvanmedia
Facebook: www.facebook.com/trelvanmedia

3. Our Services
Web Design
Internet Marketing
Website Management

```html
<!DOCTYPE html>
<html lang="en">
<head>
<meta charset="utf-8">
<title>Trelvan Media – Business Card</title>
<link href="https://fonts.googleapis.com/css2?family=Lato:wght@400;700;900&display=swap" rel="stylesheet">
<style>
  :root {
    --bg: #d9d4cc;
    --paper: #f1f1f0;
    --ink: #1e1e1e;
    --ink-soft: #333;
    --orange: #e08a1e;
    --teal: #1f7fae;
    --navy-deep: #050c2a;
    --navy: #0f2a8a;
    --sky: #3db4e4;
    --sky-light: #7fd3f2;
    --muted: #7a7a7a;
  }
  * { box-sizing: border-box; margin: 0; padding: 0; }
  html, body { width: 1200px; height: 720px; overflow: hidden; }
  body {
    background: var(--bg);
    font-family: "Lato", sans-serif;
    display: flex;
    align-items: center;
    justify-content: center;
    gap: 40px;
  }
  .card {
    width: 540px;
    height: 309px;
    border-radius: 14px;
    position: relative;
    overflow: hidden;
    box-shadow: 0 6px 18px rgba(0,0,0,.18);
  }
  /* front */
  .card--front { background: var(--paper); color: var(--ink); }
  .brand {
    position: absolute;
    font-weight: 900;
    letter-spacing: .5px;
    display: flex;
    align-items: center;
    gap: 10px;
  }
  .brand__dot { width: 26px; height: 26px; border-radius: 50%; background: var(--orange); flex: none; }
  .card--front .brand { left: 30px; top: 62px; font-size: 28px; color: var(--teal); }
  .social { position: absolute; right: 30px; top: 28px; list-style: none; font-size: 13px; color: var(--ink-soft); }
  .social li { display: flex; align-items: center; gap: 8px; margin-bottom: 7px; }
  .social__icon { width: 14px; height: 14px; background: var(--teal); border-radius: 2px; }
  .rule { position: absolute; left: 30px; right: 30px; border-top: 2px dotted #9a9a9a; }
  .rule--top { top: 120px; }
  .rule--bottom { top: 190px; right: 300px; }
  .person { position: absolute; left: 30px; top: 150px; font-size: 18px; color: var(--ink); }
  .person__name { font-weight: 700; font-size: 23px; }
  .contact { position: absolute; left: 30px; top: 204px; list-style: none; font-size: 14px; line-height: 1.5; color: var(--ink-soft); }
  .contact b { font-weight: 400; display: inline-block; width: 18px; }
  /* back */
  .card--back {
    background: radial-gradient(ellipse at 50% 35%, var(--navy) 0%, #0a1a5c 45%, var(--navy-deep) 100%);
    color: #fff;
  }
  .card--back .brand { left: 0; right: 0; justify-content: center; top: 82px; font-size: 42px; color: #fff; }
  .card--back .brand__dot { width: 34px; height: 34px; }
  .services { position: absolute; left: 0; right: 0; top: 160px; text-align: center; font-size: 14px; color: #e8ecf7; letter-spacing: .3px; }
  .services span + span::before { content: "|"; margin: 0 10px; color: #9fb0d8; }
  .band {
    position: absolute; left: 0; right: 0; top: 205px; height: 52px;
    background: linear-gradient(180deg, var(--sky-light), var(--sky));
    display: flex; align-items: center; justify-content: center;
    font-weight: 700; font-size: 18px; color: var(--navy-deep);
  }
  .band::before {
    content: ""; position: absolute; top: -1px; left: 50%; transform: translateX(-50%);
    border-left: 9px solid transparent; border-right: 9px solid transparent; border-top: 9px solid #0a1a5c;
  }
  .base { position: absolute; left: 0; right: 0; top: 257px; bottom: 0; background: var(--navy-deep); }
</style>
</head>
<body>
  <section class="card card--front">
    <div class="brand"><span class="brand__dot"></span>Trelvan Media</div>
    <ul class="social">
      <li><span class="social__icon"></span>@trelvanmedia</li>
      <li><span class="social__icon"></span>/trelvanmedia</li>
    </ul>
    <div class="rule rule--top"></div>
    <p class="person"><span class="person__name">Mark Lenner</span> / President / CEO</p>
    <div class="rule rule--bottom"></div>
    <ul class="contact">
      <li><b>T:</b> 520-381-7459</li>
      <li><b>T:</b> 866-381-7459 (free)</li>
      <li><b>E:</b> mark@trelvanmedia.example</li>
      <li>4315 W. Calloway Ave. Ste. 140, Tucson, AZ 85792</li>
    </ul>
  </section>

  <section class="card card--back">
    <div class="brand"><span class="brand__dot"></span>Trelvan Media</div>
    <p class="services"><span>Web Design</span><span>Internet Marketing</span><span>Website Management</span></p>
    <div class="band">www.trelvanmedia.example</div>
    <div class="base"></div>
  </section>
</body>
</html>
```